Business card for law firm

Need business card for new law firm. Think confident, authoritative, conservative, but not stuffy or old-fashioned.

Contact Information for Business Card

Content for card - logo (uploaded), plus the following:

Paul Whitcombe (larger font)
Managing Partner (larger font, but not as large as name)
Level 9, 7 Ferris Lane
Sydney NSW 2000
Main Tel 02 9364 2710
Direct Tel 02 8472 3159
Email paul@qvlegal.com.au
www.qvlegal.com.au

Letterhead design should include logo plus:
Level 9, 7 Ferris Lane
Sydney NSW 2000
Tel 02 8472 3159
www.qvlegal.com.au

```html
<!DOCTYPE html>
<html lang="en">
<head>
<meta charset="utf-8">
<title>Quayvale Legal – Business Card</title>
<link href="https://fonts.googleapis.com/css2?family=Open+Sans:wght@400;600;700&display=swap" rel="stylesheet">
<style>
  :root {
    --navy: #001c54;
    --ink: #1d1d1f;
    --white: #ffffff;
    --bg-top: #ececee;
    --bg-bottom: #c6c7c9;
    --rule: #9a9a9a;
  }
  * { margin: 0; padding: 0; box-sizing: border-box; }
  html, body { width: 1200px; height: 1080px; overflow: hidden; }
  body {
    position: relative;
    background: linear-gradient(160deg, var(--bg-top) 0%, var(--bg-bottom) 100%);
    font-family: "Open Sans", Arial, sans-serif;
    color: var(--ink);
  }
  .card {
    position: absolute;
    width: 778px;
    height: 444px;
    border-radius: 32px;
    overflow: hidden;
  }
  /* Front */
  .card-front {
    left: 74px; top: 71px;
    background: var(--white);
    border: 1px solid #b8b8b8;
  }
  .footer-band {
    position: absolute;
    left: 0; right: 0; bottom: 0;
    height: 92px;
    background: var(--navy);
  }
  .footer-rule {
    position: absolute;
    left: 0; right: 0; bottom: 100px;
    height: 3px;
    background: var(--navy);
  }
  .brand {
    position: absolute;
    left: 20px; width: 420px; top: 158px;
    display: flex; align-items: center; justify-content: center; gap: 12px;
    white-space: nowrap;
  }
  .brand-mark { width: 26px; height: 26px; background: var(--navy); flex: none; }
  .brand-name {
    font-weight: 600;
    font-size: 34px;
    letter-spacing: 2px;
    color: var(--navy);
    text-transform: uppercase;
  }
  .divider {
    position: absolute;
    left: 450px; top: 78px;
    width: 2px; height: 206px;
    background: var(--rule);
  }
  .contact {
    position: absolute;
    left: 477px; top: 76px;
    font-size: 21px;
    line-height: 1.45;
    color: var(--ink);
    list-style: none;
  }
  .contact .address { display: block; margin-bottom: 14px; }
  .contact li { display: flex; align-items: center; gap: 7px; height: 34px; }
  .contact li.address { height: auto; }
  .contact .icon { width: 17px; height: 17px; flex: none; fill: var(--navy); }
  .holder {
    position: absolute;
    left: 79px; top: 368px;
    color: var(--white);
  }
  .holder-name { font-weight: 700; font-size: 26px; letter-spacing: 0.5px; text-transform: uppercase; }
  .holder-role { font-size: 18px; letter-spacing: 0.5px; text-transform: uppercase; margin-top: 2px; margin-left: 11px; }

  /* Back */
  .card-back {
    left: 356px; top: 572px;
    background: var(--navy);
  }
  .back-brand {
    position: absolute;
    left: 0; width: 435px; top: 66px;
    text-align: center;
    font-weight: 600;
    font-size: 38px;
    letter-spacing: 2px;
    color: var(--white);
    text-transform: uppercase;
    white-space: nowrap;
  }
  .back-url {
    position: absolute;
    right: 78px; top: 380px;
    font-size: 22px;
    letter-spacing: 4px;
    color: var(--white);
  }
  .back-url strong { font-weight: 700; }
</style>
</head>
<body>

<section class="card card-front" aria-label="Business card front">
  <div class="footer-rule"></div>
  <div class="footer-band"></div>

  <div class="brand">
    <span class="brand-mark"></span>
    <span class="brand-name">Quayvale Legal</span>
  </div>

  <div class="divider"></div>

  <ul class="contact">
    <li class="address">Level 9, 7 Ferris Lane<br>Sydney NSW 2000</li>
    <li>
      <svg class="icon" viewBox="0 0 24 24" aria-hidden="true"><path d="M6.6 10.8a15.1 15.1 0 0 0 6.6 6.6l2.2-2.2a1 1 0 0 1 1-.25 11.4 11.4 0 0 0 3.6.57 1 1 0 0 1 1 1V20a1 1 0 0 1-1 1A17 17 0 0 1 3 4a1 1 0 0 1 1-1h3.5a1 1 0 0 1 1 1c0 1.25.2 2.45.57 3.57a1 1 0 0 1-.25 1z"/></svg>
      02 9364 2710(Main)
    </li>
    <li>
      <svg class="icon" viewBox="0 0 24 24" aria-hidden="true"><path d="M6.6 10.8a15.1 15.1 0 0 0 6.6 6.6l2.2-2.2a1 1 0 0 1 1-.25 11.4 11.4 0 0 0 3.6.57 1 1 0 0 1 1 1V20a1 1 0 0 1-1 1A17 17 0 0 1 3 4a1 1 0 0 1 1-1h3.5a1 1 0 0 1 1 1c0 1.25.2 2.45.57 3.57a1 1 0 0 1-.25 1z"/></svg>
      02 8472 3159(Direct)
    </li>
    <li>
      <svg class="icon" viewBox="0 0 24 24" aria-hidden="true"><path d="M2 6h20v13H2z M2 6l10 7 10-7" fill="none" stroke="var(--navy)" stroke-width="2.4"/></svg>
      paul@qvlegal.com.au
    </li>
    <li>
      <svg class="icon" viewBox="0 0 24 24" aria-hidden="true"><g fill="none" stroke="var(--navy)" stroke-width="2"><circle cx="12" cy="12" r="9.5"/><ellipse cx="12" cy="12" rx="4.5" ry="9.5"/><path d="M2.5 12h19M4 7h16M4 17h16"/></g></svg>
      www.qvlegal.com.au
    </li>
  </ul>

  <div class="holder">
    <div class="holder-name">Paul Whitcombe</div>
    <div class="holder-role">Managing Partner</div>
  </div>
</section>

<section class="card card-back" aria-label="Business card back">
  <div class="back-brand">Quayvale Legal</div>
  <div class="back-url">www.<strong>qvlegal</strong>.com.au</div>
</section>

</body>
</html>
```